Beacon Advisory Website

I currently have a website www.beaconadvisoryinc.com. We are a IT Consulting Company. Our website will pretty much tell out our services. I am looking to enhance my website and make it look more professional. Looking for very classy and Contemporary look and design for my website.

It Company

```html
<!DOCTYPE html>
<html lang="en">
<head>
<meta charset="utf-8">
<title>Beacon Advisory</title>
<link rel="stylesheet" href="https://fonts.googleapis.com/css2?family=Lato:wght@400;700;900&display=swap">
<style>
:root{
  --sky:#0a9bd7;
  --navy:#0d3a85;
  --royal:#1a4fa0;
  --nav:#3a3a3a;
  --nav-line:#4a4a4a;
  --ink:#333;
  --heading:#2a2a2a;
  --footer:#3c3c3c;
  --white:#fff;
}
*{box-sizing:border-box;margin:0;padding:0}
html,body{width:1147px;height:1200px;overflow:hidden;background:#fff;font-family:'Lato',sans-serif;color:var(--ink)}
.page{position:relative;width:1147px;height:1200px}
.abs{position:absolute}

.topbar{left:0;top:0;width:1147px;height:33px;background:var(--sky)}
.social-top{right:94px;top:0;display:flex}
.social-top span{width:35px;height:33px;background:var(--navy);margin-left:1px;display:flex;align-items:center;justify-content:center}
.social-top span i{width:12px;height:12px;border-radius:50%;background:rgba(255,255,255,.85)}

.brand{left:94px;top:52px;display:flex;align-items:center;gap:10px}
.brand-dot{width:40px;height:40px;border-radius:50%;background:var(--royal)}
.brand-name{font-size:24px;font-weight:900;color:var(--royal);letter-spacing:.5px;text-transform:uppercase}

.phone{right:94px;top:62px;display:flex;align-items:center;gap:8px;font-size:18px;color:#333}

.mainnav{left:0;top:115px;width:1147px;height:41px;background:var(--nav)}
.mainnav ul{list-style:none;position:absolute;left:94px;top:0;display:flex;height:41px}
.mainnav li{display:flex;align-items:center;justify-content:center;color:#fff;font-size:15px;border-right:1px solid var(--nav-line);height:41px}
.mainnav li:last-child{border-right:0}
.mainnav li.active{background:var(--sky);position:relative}
.mainnav li.active::after{content:"";position:absolute;bottom:0;left:50%;margin-left:-6px;border:6px solid transparent;border-bottom-color:#fff;border-top:0}

.hero{left:0;top:156px;width:1147px;height:450px;background:radial-gradient(circle at 85% 25%,#f3b53a 0,#a2702c 12%,#2c4f74 30%,#18344f 55%,#0e1d2e 100%)}
.hero-band{left:0;top:432px;width:1147px;height:174px;background:linear-gradient(180deg,rgba(28,86,168,.92),rgba(24,76,150,.95))}
.hero-title{left:0;top:450px;width:1147px;text-align:center;color:#fff;font-size:30px;font-weight:900}
.hero-rule{left:232px;top:497px;width:683px;height:1px;background:rgba(255,255,255,.6)}
.hero-notch{left:565px;top:497px;border:8px solid transparent;border-top-color:#fff;border-bottom:0}
.hero-text{left:100px;top:516px;width:947px;text-align:center;color:#fff;font-size:12px;font-weight:700;line-height:18.5px}
.hero-more{left:555px;top:586px;width:36px;height:20px;background:#fff;border-radius:3px 3px 0 0;text-align:center;font-size:20px;line-height:20px;color:#555}

.card{top:650px;width:295px;height:351px;background:#fff;border-top:3px solid var(--navy);box-shadow:0 2px 5px rgba(0,0,0,.15)}
.card-head{position:absolute;left:14px;top:16px;display:flex;align-items:center;gap:12px}
.card-icon{width:38px;height:38px;border-radius:50%;background:#2f2f2f;display:flex;align-items:center;justify-content:center}
.card-title{font-size:25px;font-weight:700;color:var(--heading);text-transform:uppercase}
.card-title b{color:var(--navy);font-weight:700}
.card-media{position:absolute;left:14px;top:68px;width:269px;height:118px;border:1px solid #ccc}
.card-text{position:absolute;left:14px;font-size:11.5px;line-height:17.2px;color:#333;letter-spacing:.2px}
.card-plus{position:absolute;right:0;bottom:0;width:25px;height:25px;background:var(--navy);color:#fff;text-align:center;font-size:22px;line-height:24px;font-weight:700}
.list{position:absolute;left:14px;top:170px;width:208px;list-style:none}
.list li{display:flex;align-items:center;gap:12px;height:32px;font-size:13px;border-bottom:1px dotted #999}
.list li:last-child{border-bottom:0}
.list svg{flex:none}

.footer{left:0;top:1057px;width:1147px;height:143px;background:var(--footer);border-top:3px solid #2a2a2a}
.foot-nav{left:96px;top:1090px;color:#fff;font-size:13px;word-spacing:2px}
.news{left:94px;top:1138px;display:flex;align-items:center}
.news-icon{width:38px;height:38px;border-radius:50%;background:#3c3c3c;border:3px solid #fff;z-index:1;display:flex;align-items:center;justify-content:center}
.news-field{width:172px;height:37px;background:#fff;margin-left:-6px;padding-left:16px;font-size:12px;line-height:37px;color:#666}
.news-btn{margin-left:8px;width:97px;height:37px;background:var(--navy);color:#fff;font-size:14px;font-weight:700;text-align:center;line-height:37px;border-radius:2px}
.foot-social{left:429px;top:1144px;display:flex;gap:9px}
.foot-social span{width:26px;height:26px;border-radius:50%;background:#fff}
.foot-brand{left:848px;top:1096px;display:flex;align-items:center;gap:8px}
.foot-brand .brand-dot{background:#8a8a8a;width:34px;height:34px}
.foot-brand .brand-name{color:#9a9a9a;font-size:20px}
.copy{right:97px;top:1162px;color:#fff;font-size:12px}
</style>
</head>
<body>
<div class="page">

  <div class="abs topbar"></div>
  <div class="abs social-top" aria-label="Social links">
    <span><i></i></span><span><i></i></span><span><i></i></span><span><i></i></span>
  </div>

  <div class="abs brand"><span class="brand-dot"></span><span class="brand-name">Beacon Advisory</span></div>

  <div class="abs phone">
    <svg width="24" height="24" viewBox="0 0 24 24"><circle cx="12" cy="12" r="11" fill="none" stroke="#1a4fa0" stroke-width="2"/><path d="M8 6c1 0 2 2 2 3s-1 1-1 2 2 4 4 4 1-1 2-1 3 1 3 2-1 2-3 2C11 18 6 13 6 9c0-2 1-3 2-3z" fill="#1a4fa0"/></svg>
    555 014 2290
  </div>

  <nav class="abs mainnav">
    <ul>
      <li class="active" style="width:166px">COMPANY</li>
      <li style="width:158px">SERVICES</li>
      <li style="width:173px">SOLUTIONS</li>
      <li style="width:174px">RESOURCES</li>
      <li style="width:147px">CAREER</li>
      <li style="width:141px">CONTACT US</li>
    </ul>
  </nav>

  <div class="abs hero" role="img" aria-label="Digital technology scene with data streams, city skyline and glowing analysis dial"></div>
  <div class="abs hero-band"></div>
  <h1 class="abs hero-title">WELCOME TO BEACON ADVISORY</h1>
  <div class="abs hero-rule"></div>
  <div class="abs hero-notch"></div>
  <p class="abs hero-text">Today's IT market is a dynamic, fast-paced industry, with ever-increasing demands. Meeting these demands for over 25 years, Beacon Advisory maintains a global presence, aggressively recruiting expertly qualified IT and Management Professionals from around the world and cultivating key partnerships with corporations to understand their business models end-to-end, with a goal of delivering exceptional client service and ensuring a consistent delivery of the talent needed to drive results.</p>
  <div class="abs hero-more">+</div>

  <section class="abs card" style="left:94px">
    <div class="card-head">
      <span class="card-icon"><svg width="20" height="20" viewBox="0 0 20 20"><circle cx="10" cy="10" r="4" fill="#fff"/><g stroke="#fff" stroke-width="1.6"><path d="M10 1v3M10 16v3M1 10h3M16 10h3M3.6 3.6l2 2M14.4 14.4l2 2M3.6 16.4l2-2M14.4 5.6l2-2"/></g></svg></span>
      <h2 class="card-title"><b>IT</b> CONSULTING</h2>
    </div>
    <div class="card-media" role="img" aria-label="Photo of a consultant working on a laptop in a bright office" style="background:linear-gradient(90deg,#b9c6d6,#e8eef2 60%,#cfd9df)"></div>
    <p class="card-text" style="top:199px;width:272px">Information technology should improve business results. Northfield helps companies make sure it does. We look at IT issues strategically, in the broader context of our clients' business. Our experts provide an objective, independent perspective to help companies realize the full potential of their IT resources, investments and assets.</p>
    <div class="card-plus">+</div>
  </section>

  <section class="abs card" style="left:428px;width:296px">
    <div class="card-head">
      <span class="card-icon"><svg width="18" height="20" viewBox="0 0 18 20"><rect x="3" y="2" width="12" height="16" rx="1" fill="none" stroke="#fff" stroke-width="1.6"/><path d="M6 7h6M6 10h6M6 13h4" stroke="#fff" stroke-width="1.4"/></svg></span>
      <h2 class="card-title"><b>WHAT</b> WE DO</h2>
    </div>
    <p class="card-text" style="top:66px;width:274px">We are successful in deploying all students we trained into project with 2-3 weeks after training program. Our training programs will last for 6-8 weeks dependents on technology. We will provide on job support for trainees until technology comfort level is attained.</p>
    <ul class="list">
      <li><svg width="20" height="20" viewBox="0 0 20 20"><circle cx="8" cy="12" r="5" fill="none" stroke="#1a4fa0" stroke-width="2"/><circle cx="15" cy="5" r="3" fill="none" stroke="#1a4fa0" stroke-width="2"/></svg>Technology</li>
      <li><svg width="20" height="20" viewBox="0 0 20 20"><circle cx="10" cy="4" r="2.5" fill="#1a4fa0"/><rect x="7" y="8" width="6" height="11" fill="#1a4fa0"/><rect x="1" y="10" width="4" height="9" fill="#1a4fa0"/><rect x="15" y="10" width="4" height="9" fill="#1a4fa0"/></svg>Offshore Business</li>
      <li><svg width="20" height="20" viewBox="0 0 20 20"><rect x="4" y="1" width="11" height="18" rx="2" fill="none" stroke="#1a4fa0" stroke-width="2"/><circle cx="11" cy="11" r="3" fill="#1a4fa0"/></svg>Application Developement</li>
      <li><svg width="20" height="20" viewBox="0 0 20 20"><g fill="none" stroke="#1a4fa0" stroke-width="1.6"><circle cx="10" cy="5" r="3"/><circle cx="5" cy="13" r="3"/><circle cx="15" cy="13" r="3"/></g></svg>Enterprise Integration</li>
      <li><svg width="20" height="20" viewBox="0 0 20 20"><circle cx="10" cy="10" r="5" fill="none" stroke="#1a4fa0" stroke-width="2"/><path d="M10 1v4M10 15v4M1 10h4M15 10h4" stroke="#1a4fa0" stroke-width="2"/></svg>IT Consulting</li>
    </ul>
    <div class="card-plus">+</div>
  </section>

  <section class="abs card" style="left:759px;width:294px">
    <div class="card-head">
      <span class="card-icon"><svg width="20" height="20" viewBox="0 0 20 20"><circle cx="10" cy="10" r="5" fill="none" stroke="#fff" stroke-width="2"/><circle cx="10" cy="10" r="2" fill="#fff"/><path d="M10 1v3M10 16v3M1 10h3M16 10h3" stroke="#fff" stroke-width="2"/></svg></span>
      <h2 class="card-title"><b>OFF</b>SHORE</h2>
    </div>
    <div class="card-media" role="img" aria-label="Blue world map with glowing connection lines across continents" style="background:linear-gradient(135deg,#0c3f78,#2d8ac8 55%,#0f4e8c)"></div>
    <p class="card-text" style="top:199px;width:274px">Our Offshore development model has a unique distinction of providing efficient software solutions with cost and quality advantage, using state-of-the-art technologies, having the capacity to handle large projects and, above all, the ability to execute timely deliveries.</p>
    <div class="card-plus">+</div>
  </section>

  <footer class="abs footer"></footer>
  <div class="abs foot-nav">COMPANY &nbsp;/&nbsp; SERVICES &nbsp;/&nbsp; SOLUTIONS &nbsp;/&nbsp; RESOURCES &nbsp;/&nbsp; CAREER &nbsp;/&nbsp; CONTACT US</div>
  <div class="abs news">
    <span class="news-icon"><svg width="18" height="13" viewBox="0 0 18 13"><rect x="1" y="1" width="16" height="11" fill="none" stroke="#fff" stroke-width="1.6"/><path d="M1 1l8 6 8-6" fill="none" stroke="#fff" stroke-width="1.6"/></svg></span>
    <span class="news-field">Sign Up for Newsletter</span>
    <span class="news-btn">SUBSCRIBE</span>
  </div>
  <div class="abs foot-social" aria-label="Social links"><span></span><span></span><span></span><span></span></div>
  <div class="abs foot-brand"><span class="brand-dot"></span><span class="brand-name">Beacon Advisory</span></div>
  <div class="abs copy">© 2016 BeaconAdvisory. All Right Reserved.</div>

</div>
</body>
</html>
```